BOLD & MINIMALIST DESIGN NEEDED

We want a very bold but minimalistic business card design that is impactful and utilizes both sides of the business card. Our current logo is included for your use.

We want bold fonts and good use of negative space. We don't want the logo to overpower the design.

Target Market(s)

Professionals who are building new commercial buildings.

Industry/Entity Type

Construction

Contact Information for Business Card

Name, Title, email, office phone, cell phone, website

Font styles to use
Serif
Sans Serif

Requirements
Must have
• Bold design!

```html
<!DOCTYPE html>
<html lang="en">
<head>
<meta charset="utf-8">
<title>Ridgeline Build – Business Card</title>
<link href="https://fonts.googleapis.com/css2?family=Arimo:wght@400;700&display=swap" rel="stylesheet">
<style>
  :root {
    --page-bg: #1c1c1c;
    --card-white: #f4f4f4;
    --brand-green: #7dbf3f;
    --ink-dark: #1f1f1f;
    --ink-text: #333333;
    --rule-green: #a9d47f;
  }
  * { margin: 0; padding: 0; box-sizing: border-box; }
  html, body {
    width: 1200px; height: 1059px; overflow: hidden;
    background: var(--page-bg);
    font-family: "Arimo", Helvetica, Arial, sans-serif;
  }
  .canvas { position: relative; width: 1200px; height: 1059px; }

  .card {
    position: absolute;
    width: 690px; height: 392px;
    border-radius: 20px;
    overflow: hidden;
  }
  .card-front { left: 256px; top: 89px; background: var(--card-white); }
  .card-back  { left: 254px; top: 547px; background: var(--brand-green); }

  .brand {
    position: absolute; left: 0; right: 0;
    display: flex; align-items: center; justify-content: center;
    font-weight: 700; text-transform: uppercase; letter-spacing: 1px;
  }
  .brand-mark { display: inline-block; background: currentColor; }
  .card-front .brand { top: 92px; color: var(--ink-dark); font-size: 34px; gap: 12px; }
  .card-front .brand-mark { width: 22px; height: 22px; }
  .card-back .brand { top: 168px; color: #ffffff; font-size: 58px; gap: 18px; }
  .card-back .brand-mark { width: 38px; height: 38px; }

  .identity {
    position: absolute; right: 373px; top: 232px; text-align: right;
    white-space: nowrap;
  }
  .identity-name {
    color: var(--brand-green); font-weight: 700; font-size: 26px; line-height: 1;
  }
  .identity-title {
    color: var(--ink-text); font-size: 18px; margin-top: 6px;
  }
  .divider {
    position: absolute; left: 344px; top: 208px;
    width: 1px; height: 96px; background: var(--rule-green);
  }
  .contact-list {
    position: absolute; left: 370px; top: 204px; list-style: none;
  }
  .contact-list li {
    display: flex; align-items: center; gap: 5px;
    height: 26.5px; font-size: 18px; color: var(--ink-text); white-space: nowrap;
  }
  .contact-list svg { width: 12px; height: 12px; fill: var(--brand-green); flex: none; }

  .swoosh { position: absolute; left: 0; bottom: 0; width: 690px; height: 60px; }
</style>
</head>
<body>
<div class="canvas">

  <section class="card card-front">
    <div class="brand"><span class="brand-mark"></span>Ridgeline Build</div>

    <div class="identity">
      <div class="identity-name">DANA WHITFIELD</div>
      <div class="identity-title">Owner/CEO</div>
    </div>

    <div class="divider"></div>

    <ul class="contact-list">
      <li>
        <svg viewBox="0 0 16 16" aria-hidden="true"><path d="M3 1l3 3-1.6 2a9 9 0 0 0 5.6 5.6L12 10l3 3-2 2C6.5 15 1 9.5 1 3z"/></svg>
        07 5120 3300
      </li>
      <li>
        <svg viewBox="0 0 16 16" aria-hidden="true"><path d="M4 0h8a1 1 0 0 1 1 1v14a1 1 0 0 1-1 1H4a1 1 0 0 1-1-1V1a1 1 0 0 1 1-1zm1 2v10h6V2zm3 11a1 1 0 1 0 0 2 1 1 0 0 0 0-2z"/></svg>
        0402 557 914
      </li>
      <li>
        <svg viewBox="0 0 16 16" aria-hidden="true"><path d="M1 3h14v10H1zm1.5 1.2L8 8.5l5.5-4.3V4h-11z"/></svg>
        info@ridgelinebuild.com
      </li>
      <li>
        <svg viewBox="0 0 16 16" aria-hidden="true"><circle cx="8" cy="8" r="7"/><path d="M4 5c2 0 2 2 4 2s1 3 0 4-1 3-2 3-1-3-2-4-1-3 0-5z" fill="#fff" opacity=".6"/></svg>
        www.ridgelinebuild.com
      </li>
    </ul>

    <svg class="swoosh" viewBox="0 0 690 60" preserveAspectRatio="none" aria-hidden="true">
      <path d="M10 42 Q345 -14 680 40" fill="none" stroke="var(--brand-green)" stroke-width="3" opacity=".85"/>
      <path d="M0 60 L0 48 Q345 -6 690 48 L690 60 Z" fill="var(--ink-dark)"/>
    </svg>
  </section>

  <section class="card card-back">
    <div class="brand"><span class="brand-mark"></span>Ridgeline Build</div>
  </section>

</div>
</body>
</html>
```